Silver Harbour Agency Website Design

We are after a 6 page website for www.silverharbouragency.example
It needs to be coded and uploaded to our hosting service.

All design info + info about our business is in the attached brief. It is a guide only with the basics required however we are looking for someone with a creative eye.

UPDATE - Would prefer no gold on the website (except in the logo) as it doesn't transfer well online. Also not interested in a Word Press site.

Target Market(s)

Very broad audience. Predominately corporate businesses, male and female, 18-40 years.

Industry/Entity Type

Events

Coding

Coded - Design and coding required

Number of Pages Required

5+ page

Font styles to use
Serif
Script

Colors
ffffff

Requirements
Must have
• Mobile compatibility/easy to navigate/live Instagram feed as described in attached brief
Nice to have
• *Simple/minimalist design yet still very creative and imaginative.
• *Elegant & professional - not basic
Should not have
• *Too much information/photos
• *Lots of colour
• *Lots of unnecessary text

```html
<!DOCTYPE html>
<html lang="en">
<head>
<meta charset="utf-8">
<title>Silver Harbour Agency</title>
<link href="https://fonts.googleapis.com/css2?family=Great+Vibes&family=Lora:wght@400;600&display=swap" rel="stylesheet">
<style>
:root{
  --ink:#1b1b1b;
  --muted:#555;
  --paper:#ffffff;
  --rule:#cfcfcf;
  --band-top:#d9d9d9;
  --band-bottom:#9c9c9c;
  --badge-fill:rgba(20,20,20,0.72);
  --foot-top:#ffffff;
  --foot-bottom:#d6d6d6;
}
*{box-sizing:border-box;margin:0;padding:0}
html,body{width:814px;height:1200px;overflow:hidden;background:var(--paper)}
body{font-family:"Lora",Georgia,serif;color:var(--ink)}
.page{position:relative;width:814px;height:1200px;overflow:hidden;
  background:linear-gradient(#fff 0,#fff 1000px,var(--foot-top) 1000px,var(--foot-bottom) 1200px)}

.brand{position:absolute;top:30px;left:0;width:814px;display:flex;justify-content:center;align-items:center;gap:12px}
.brand-dot{width:18px;height:18px;border-radius:50%;background:var(--ink)}
.brand-name{font-family:"Great Vibes",cursive;font-size:42px;color:var(--ink);line-height:1}

.main-nav{position:absolute;top:110px;left:54px;width:711px;border-bottom:1px solid var(--rule);
  display:flex;justify-content:space-between;padding:0 96px 8px}
.main-nav a{font-size:13px;color:var(--ink);text-decoration:none;position:relative;font-style:italic}
.main-nav a.active::after{content:"";position:absolute;left:-10px;right:-10px;bottom:-10px;height:3px;background:var(--ink)}

.slider{position:absolute;top:150px;left:54px;width:711px;height:276px;
  background:radial-gradient(circle at 50% 40%,#6e6e6e 0,#3a3a3a 45%,#1a1a1a 100%)}
.slider-arrow{position:absolute;top:118px;width:24px;height:40px}
.slider-arrow.prev{left:14px}
.slider-arrow.next{right:14px}
.slider-dots{position:absolute;top:436px;left:0;width:814px;display:flex;justify-content:center;gap:7px}
.slider-dots span{width:7px;height:7px;border-radius:50%;background:#bbb}
.slider-dots span.on{background:#555}

.section-title{position:absolute;left:0;width:814px;text-align:center;font-family:"Great Vibes",cursive;font-size:34px;font-weight:400;color:var(--ink)}
.divider{position:absolute;left:307px;width:200px;height:14px}

.welcome-title{top:470px}
.welcome-divider{top:510px}
.team-photo{position:absolute;top:543px;left:95px;width:230px;height:150px;
  background:linear-gradient(160deg,#cfd6dc,#6d7a88 55%,#2a3448)}
.welcome-text{position:absolute;top:540px;left:345px;width:420px;font-size:11px;line-height:17px;color:var(--muted)}
.welcome-text p+p{margin-top:2px}

.services{position:absolute;top:720px;left:49px;width:721px;height:270px;
  background:linear-gradient(var(--band-top),var(--band-bottom))}
.services-title{top:742px}
.services-divider{top:780px}
.stats{position:absolute;top:806px;left:49px;width:721px;display:flex;justify-content:space-around;padding:0 40px}
.stat{width:120px;text-align:center}
.stat svg{display:block;width:120px;height:104px}
.stat-label{font-size:11px;color:#fff;margin-top:6px}
.services-note{position:absolute;top:950px;left:110px;width:600px;text-align:center;font-size:10px;line-height:15px;color:#f2f2f2}

.contact-phone{position:absolute;top:1034px;left:0;width:814px;text-align:center;font-size:34px;letter-spacing:1px;color:var(--ink)}
.contact-email{position:absolute;top:1082px;left:0;width:814px;text-align:center;font-size:12px;font-style:italic;color:var(--muted)}
.social{position:absolute;top:1110px;left:0;width:814px;display:flex;justify-content:center;gap:14px}
.social span{width:32px;height:32px;border-radius:50%;background:#333}
.copyright{position:absolute;top:1172px;left:0;width:814px;text-align:center;font-size:10px;color:var(--muted)}
</style>
</head>
<body>
<div class="page">
  <header>
    <div class="brand"><span class="brand-dot"></span><span class="brand-name">Silver Harbour Agency</span></div>
    <nav class="main-nav">
      <a class="active" href="#">Home</a><a href="#">About Us</a><a href="#">Testimonials</a><a href="#">Join</a><a href="#">Get Social</a><a href="#">Contact</a>
    </nav>
  </header>

  <section class="slider" role="img" aria-label="Event photograph: ring hostess holding a round card above her head in a dark arena">
    <svg class="slider-arrow prev" viewBox="0 0 24 40"><polyline points="18,6 6,20 18,34" fill="none" stroke="#fff" stroke-width="4"/></svg>
    <svg class="slider-arrow next" viewBox="0 0 24 40"><polyline points="6,6 18,20 6,34" fill="none" stroke="#fff" stroke-width="4"/></svg>
  </section>
  <div class="slider-dots"><span class="on"></span><span></span><span></span><span></span></div>

  <h1 class="section-title welcome-title">Welcome To Silver Harbour Agency</h1>
  <svg class="divider welcome-divider" viewBox="0 0 200 14"><line x1="0" y1="7" x2="200" y2="7" stroke="#333" stroke-width="1"/><circle cx="100" cy="7" r="5" fill="#1b1b1b"/></svg>
  <div class="team-photo" role="img" aria-label="Photograph of four promotional staff in navy uniforms standing together"></div>
  <div class="welcome-text">
    <p>Silver Harbour Agency can staff promotional and brand ambassadors to any event including (but not limited to) trade shows, pub club birthday promotions, sampling, golf days, trade show expos, conferences, concerts, sporting events, boxing/MMA fights, and corporate events. We can also run the event management side of activations and assist with all logistics.</p>
    <p>Silver Harbour Agency is currently based between Sydney &amp; Newcastle, NSW and can staff any event no matter how big or small, Australia wide.</p>
  </div>

  <section class="services"></section>
  <h2 class="section-title services-title">Services</h2>
  <svg class="divider services-divider" viewBox="0 0 200 14"><line x1="0" y1="7" x2="200" y2="7" stroke="#222" stroke-width="1"/><circle cx="100" cy="7" r="5" fill="#1b1b1b"/></svg>
  <div class="stats">
    <div class="stat"><svg viewBox="0 0 120 104"><circle cx="60" cy="52" r="46" fill="var(--badge-fill)" stroke="#fff" stroke-width="5"/><text x="60" y="62" text-anchor="middle" font-family="Lora,serif" font-size="28" fill="#fff">600</text></svg><div class="stat-label">Elite Staff</div></div>
    <div class="stat"><svg viewBox="0 0 120 104"><circle cx="60" cy="52" r="46" fill="var(--badge-fill)" stroke="#fff" stroke-width="5"/><text x="60" y="62" text-anchor="middle" font-family="Lora,serif" font-size="28" fill="#fff">600</text></svg><div class="stat-label">Female Staff</div></div>
    <div class="stat"><svg viewBox="0 0 120 104"><circle cx="60" cy="52" r="46" fill="var(--badge-fill)" stroke="#fff" stroke-width="5"/><text x="60" y="62" text-anchor="middle" font-family="Lora,serif" font-size="28" fill="#fff">500</text></svg><div class="stat-label">Auxiliary Staff</div></div>
    <div class="stat"><svg viewBox="0 0 120 104"><circle cx="60" cy="52" r="46" fill="var(--badge-fill)" stroke="#fff" stroke-width="5"/><text x="60" y="62" text-anchor="middle" font-family="Lora,serif" font-size="28" fill="#fff">80%</text></svg><div class="stat-label">Satisfied Clients</div></div>
  </div>
  <p class="services-note">Our staff are carefully selected and trained for work across all fields: events, promotions, advertising, marketing, communications and PR agencies in NSW, ensuring professional service. Rates are available upon request.</p>

  <footer>
    <div class="contact-phone">0400 555 012</div>
    <div class="contact-email">info@silverharbouragency.example</div>
    <div class="social"><span></span><span></span><span></span><span></span></div>
    <div class="copyright">© 2016 Silver Harbour Agency. All Rights Reserved</div>
  </footer>
</div>
</body>
</html>
```